Digital Marketing Agency Landing Page

At VELIM, we offer a comprehensive solution for solar companies' client acquisition needs in the rapidly growing industry. We handle end-to-end client acquisition, meaning we manage the entire lifecycle of capturing new clients—from initial lead generation to delivering the ready-to-buy homeowner. Our expertise in targeted advertising, data analytics, and customer relationship management ensures that we not only find potential customers but also nurture them through tailored engagement strategies until they are ready to make a purchase. By entrusting us with your client acquisition process, solar companies can focus on what they do best—providing sustainable energy solutions—while we work behind the scenes to grow your customer base and increase your market share.

We need to restructure our website to make it more professional. We don't need any complex functionalities. We are looking for someone that is good in design and can build a visually aesthetic website following our brand image. We only need a landing page and a lead form in the end. I would like to have only one page, but a relatively big one where people scroll down. I would like to have a minimal and classy look. Something that is timeless and elegant.

Structure:

initial page
About us
How we operate
Get in touch

Target Market(s)

Solar Comapanies

Industry/Entity Type

Marketing solautions

Coding

Coded - Design and coding required

Number of Pages Required

1 page

Requirements
Nice to have
• Inspirations: https://www.qz.zu/ https://www.marchbeck.example/ https://www.tovanrid.example/ https://pruvo.example/

```html
<!DOCTYPE html>
<html lang="en">
<head>
<meta charset="utf-8">
<title>VELIM — Solar Client Acquisition</title>
<link rel="stylesheet" href="https://fonts.googleapis.com/css2?family=Montserrat:wght@300;400;500;600&family=Lato:wght@400&display=swap">
<style>
:root{
  --navy:#13233a;
  --navy-deep:#0b111c;
  --ink:#102033;
  --cream:#ece6dc;
  --cream-line:#e6ddcc;
  --white:#ffffff;
  --muted:#6b7380;
}
*{margin:0;padding:0;box-sizing:border-box}
html,body{width:1200px;height:2195px;overflow:hidden}
body{position:relative;font-family:'Montserrat',sans-serif;background:var(--white);color:var(--ink)}
.abs{position:absolute}
a{color:inherit;text-decoration:none}

/* hero */
.hero{left:0;top:0;width:1200px;height:642px;
  background:linear-gradient(100deg,#2a3f4c 0%,#1f3550 35%,#1a2d5c 65%,#1b2a55 100%)}
.hero-photo{left:0;top:0;width:1200px;height:642px;
  background:radial-gradient(ellipse at 20% 10%,rgba(120,150,150,.35),transparent 60%),
             linear-gradient(180deg,rgba(40,70,80,.3),rgba(15,25,60,.5))}
.wordmark{color:var(--cream);font-weight:300;letter-spacing:2px;line-height:1}
.nav-link{top:50px;color:var(--white);font-size:15px;font-weight:400;letter-spacing:.3px}
.frame-btn{border:1px solid var(--cream-line);color:var(--white);display:flex;align-items:center;justify-content:center;font-weight:500;letter-spacing:.3px}
.frame-btn::after{content:"";position:absolute;border:1px solid var(--cream-line);left:10px;top:8px;right:-10px;bottom:-8px}
.hero-title{left:110px;top:200px;width:520px;color:var(--cream);font-size:34px;font-weight:500;line-height:56px;letter-spacing:.8px;text-transform:uppercase}
.form-frame{border:2px solid var(--cream-line)}
.form-title{left:688px;top:218px;width:375px;text-align:center;color:var(--cream);font-size:27px;font-weight:400;letter-spacing:.6px}
.field{left:716px;width:317px;height:47px;background:var(--white);font-size:12px;color:var(--muted);padding-left:18px;display:flex;align-items:center;letter-spacing:.4px}
.submit{left:799px;top:451px;width:152px;height:46px;background:var(--cream);color:var(--ink);font-size:14px;font-weight:600;display:flex;align-items:center;justify-content:center}

/* services */
.section-title{font-size:33px;font-weight:500;letter-spacing:1px;color:var(--ink);text-align:center}
.card{top:771px;width:303px;height:428px;border:3px solid var(--ink)}
.card.light{border:2px solid var(--cream-line)}
.card-inner{position:absolute;left:9px;top:9px;right:9px;bottom:9px;background:linear-gradient(180deg,#132538,#14273b 60%,#112233);display:flex;flex-direction:column;align-items:center;color:var(--white);text-align:center}
.card.light .card-inner{background:linear-gradient(180deg,#efece6,#ebe7e0);color:var(--ink);left:10px;top:10px;right:10px;bottom:10px}
.card-icon{margin-top:36px;height:96px;display:flex;align-items:center}
.card-title{margin-top:14px;font-size:17px;font-weight:600;letter-spacing:.3px;line-height:31px;padding:0 8px}
.card-text{margin-top:10px;font-family:'Lato',sans-serif;font-size:14px;line-height:29px;padding:0 22px}
.card-link{position:absolute;bottom:32px;font-size:14px;font-weight:500;text-decoration:underline;text-underline-offset:3px}

/* about */
.about{left:0;top:1273px;width:1200px;height:495px;background:var(--navy)}
.about-photo{left:0;top:1273px;width:720px;height:495px;
  background:linear-gradient(90deg,#1f4a7e 0%,#1d3f6d 45%,rgba(20,36,58,0) 100%)}
.about-title{left:611px;top:1335px;color:var(--white);font-size:36px;font-weight:500;letter-spacing:.6px}
.about-text{left:611px;width:480px;color:var(--white);font-family:'Lato',sans-serif;font-size:15px;line-height:29px}

/* footer */
.footer{left:0;top:1768px;width:1200px;height:365px;background:var(--navy-deep)}
.foot-link{top:1999px;color:var(--white);font-size:15px;letter-spacing:.3px}
.contact-item{top:2062px;color:var(--white);font-size:15px;display:flex;align-items:center;gap:10px}
.copyright{left:0;top:2133px;width:1200px;height:62px;background:var(--cream);display:flex;align-items:center;justify-content:center;font-size:14px;font-weight:600;color:var(--ink);letter-spacing:.3px}
</style>
</head>
<body>

<!-- hero -->
<div class="abs hero"></div>
<div class="abs hero-photo" role="img" aria-label="Wind turbines and rows of solar panels at dusk"></div>

<div class="abs wordmark" style="left:112px;top:40px;font-size:36px">VELIM</div>
<a class="abs nav-link" style="left:426px">HOME</a>
<a class="abs nav-link" style="left:543px">ABOUT US</a>
<a class="abs nav-link" style="left:694px">SERVICES</a>
<a class="abs frame-btn" style="left:946px;top:36px;width:134px;height:41px;font-size:13px">CONTACT US</a>

<h1 class="abs hero-title">Bridging the gap between solar experts and value-driven homeowners</h1>
<a class="abs frame-btn" style="left:111px;top:446px;width:191px;height:48px;font-size:15px">GET STARTED</a>

<div class="abs form-frame" style="left:662px;top:162px;width:401px;height:369px"></div>
<div class="abs form-frame" style="left:688px;top:188px;width:400px;height:369px"></div>
<h2 class="abs form-title">CONTACT US</h2>
<div class="abs field" style="top:265px">NAME</div>
<div class="abs field" style="top:325px">EMAIL</div>
<div class="abs field" style="top:385px">PHONE NUMBER</div>
<div class="abs submit">SUBMIT</div>

<!-- services -->
<h2 class="abs section-title" style="left:0;top:690px;width:1200px">OUR SERVICES</h2>

<div class="abs card" style="left:111px">
  <div class="card-inner">
    <div class="card-icon">
      <svg width="84" height="84" viewBox="0 0 84 84" fill="none" stroke="#fff" stroke-width="3">
        <circle cx="42" cy="42" r="36"/><circle cx="42" cy="42" r="22"/><circle cx="42" cy="42" r="8"/>
      </svg>
    </div>
    <div class="card-title">ADVERTISING</div>
    <p class="card-text">Temporibus autem quibusdam et aut officiis debitis aut rerum necessitatibus saepe eveniet ut et voluptates repudiandae sint et molestiae non recusandae.</p>
    <a class="card-link">LEARN MORE</a>
  </div>
</div>

<div class="abs card light" style="left:449px">
  <div class="card-inner">
    <div class="card-icon">
      <svg width="84" height="84" viewBox="0 0 84 84" fill="none" stroke="#102033" stroke-width="3" stroke-linecap="round">
        <line x1="6" y1="78" x2="78" y2="78"/>
        <rect x="12" y="50" width="12" height="28"/><rect x="32" y="34" width="12" height="44"/>
        <rect x="52" y="18" width="12" height="60"/>
      </svg>
    </div>
    <div class="card-title">DATA ANALYTICS</div>
    <p class="card-text">Itaque earum rerum hic tenetur a sapiente delectus, ut aut reiciendis voluptatibus maiores alias consequatur aut perferendis doloribus asperiores repellat.</p>
    <a class="card-link">LEARN MORE</a>
  </div>
</div>

<div class="abs card" style="left:786px">
  <div class="card-inner">
    <div class="card-icon">
      <svg width="96" height="70" viewBox="0 0 96 70" fill="none" stroke="#fff" stroke-width="3">
        <circle cx="34" cy="35" r="28"/><circle cx="62" cy="35" r="28"/>
      </svg>
    </div>
    <div class="card-title">CUSTOMER RELATIONSHIP MANAGEMENT</div>
    <p class="card-text" style="margin-top:4px">Nam libero tempore, cum soluta nobis est eligendi optio cumque nihil impedit quo minus id quod maxime quod maxime placeat facere</p>
    <a class="card-link">LEARN MORE</a>
  </div>
</div>

<!-- about -->
<div class="abs about"></div>
<div class="abs about-photo" role="img" aria-label="Hands on a laptop with glowing analytics dashboards floating above"></div>
<h2 class="abs about-title">ABOUT VELIM</h2>
<p class="abs about-text" style="top:1385px">Nam libero tempore, cum soluta nobis est eligendi optio cumque nihil impedit quo minus id quod maxime placeat facere possimus, omnis voluptas assumenda est, omnis dolor repellendus. Temporibus autem ut et voluptates repudiandae sint et molestiae non recusandae.</p>
<p class="abs about-text" style="top:1531px">Itaque earum rerum hic tenetur a sapiente delectus, ut aut reiciendis voluptatibus maiores alias consequatur aut perferendis doloribus asperiores repellat.</p>
<a class="abs frame-btn" style="left:612px;top:1637px;width:191px;height:49px;font-size:16px">READ MORE</a>

<!-- footer -->
<div class="abs footer"></div>
<div class="abs wordmark" style="left:0;top:1872px;width:1200px;text-align:center;font-size:56px">VELIM</div>
<a class="abs foot-link" style="left:300px">HOME</a>
<a class="abs foot-link" style="left:444px">ABOUT US</a>
<a class="abs foot-link" style="left:621px">SERVICES</a>
<a class="abs foot-link" style="left:793px">CONTACT US</a>

<div class="abs contact-item" style="left:300px">
  <svg width="14" height="18" viewBox="0 0 14 18"><path d="M7 0a7 7 0 0 1 7 7c0 5-7 11-7 11S0 12 0 7a7 7 0 0 1 7-7z" fill="#fff"/><circle cx="7" cy="7" r="2.5" fill="#0b111c"/></svg>
  <span>Velim, United States</span>
</div>
<div class="abs contact-item" style="left:538px">
  <svg width="16" height="16" viewBox="0 0 16 16"><path d="M3 1l3 3-2 2c1 2 3 4 5 5l2-2 3 3-2 3C7 15 1 9 1 3z" fill="#fff"/></svg>
  <span>+1 555 014 2290</span>
</div>
<div class="abs contact-item" style="left:741px">
  <svg width="18" height="14" viewBox="0 0 18 14"><rect width="18" height="14" rx="1" fill="#fff"/><path d="M1 1l8 7 8-7" fill="none" stroke="#0b111c" stroke-width="1.5"/></svg>
  <span>hello@velim.example</span>
</div>

<div class="abs copyright">COPYRIGHTS@2023.VELIM.ALL RIGHTS RESERVED</div>

</body>
</html>
```